Letterhead, stationery and email signature for construction business

I need the letterhead, stationery and email signature designs for a construction business. I want them to have a corporate feel to them.

I've attached the logo for reference.

```html
<!DOCTYPE html>
<html lang="en">
<head>
<meta charset="utf-8">
<title>Email Signature – Corven Projects</title>
<link rel="stylesheet" href="https://fonts.googleapis.com/css2?family=Montserrat:wght@400;500;700&family=Roboto:wght@400&family=Tenor+Sans&display=swap">
<style>
  :root {
    --bg: #ffffff;
    --ink-dark: #333333;
    --ink-body: #6b6b6b;
    --ink-role: #4a4a4a;
    --brand-blue: #2a56a6;
    --brand-grey: #55555f;
    --rule: #555555;
    --social-1: #3b5998;
    --social-2: #c13584;
    --social-3: #1da1f2;
    --social-4: #0a66c2;
  }
  * { margin: 0; padding: 0; box-sizing: border-box; }
  html, body {
    width: 1200px; height: 1200px; overflow: hidden;
    background: var(--bg);
  }
  .canvas { position: relative; width: 1200px; height: 1200px; }

  .page-title {
    position: absolute; top: 188px; left: 0; width: 1200px;
    text-align: center;
    font-family: "Tenor Sans", sans-serif; font-weight: 400;
    font-size: 46px; letter-spacing: 2.5px;
    color: var(--ink-dark);
  }

  .brand {
    position: absolute; left: 186px; top: 570px;
    display: flex; align-items: center; gap: 16px;
    height: 60px;
  }
  .brand-square {
    width: 60px; height: 60px; background: var(--brand-grey); flex: none;
  }
  .brand-name {
    font-family: "Montserrat", sans-serif; font-weight: 500;
    font-size: 34px; line-height: 1;
    color: var(--brand-grey); white-space: nowrap;
  }

  .divider {
    position: absolute; left: 611px; top: 408px;
    width: 2px; height: 382px; background: var(--rule);
  }

  .details { position: absolute; left: 646px; top: 412px; width: 440px; }
  .person-name {
    font-family: "Montserrat", sans-serif; font-weight: 700;
    font-size: 30px; color: var(--brand-blue); line-height: 1.2;
  }
  .person-role {
    font-family: "Roboto", sans-serif; font-size: 27px;
    color: var(--ink-role); line-height: 1.2; margin-top: 2px;
  }
  .address {
    font-family: "Montserrat", sans-serif; font-size: 25px;
    color: var(--ink-body); line-height: 32px; margin-top: 30px;
  }
  .contact-list { list-style: none; margin-top: 14px; }
  .contact-item {
    display: flex; align-items: center; gap: 8px;
    font-family: "Montserrat", sans-serif; font-size: 26px;
    color: var(--ink-body); height: 37px;
  }
  .contact-icon { width: 26px; height: 26px; flex: none; }
  .social-row { display: flex; gap: 7px; margin-top: 20px; }
  .social-dot { width: 31px; height: 31px; border-radius: 50%; }
  .social-dot.s1 { background: var(--social-1); }
  .social-dot.s2 { background: var(--social-2); }
  .social-dot.s3 { background: var(--social-3); }
  .social-dot.s4 { background: var(--social-4); }
</style>
</head>
<body>
<div class="canvas">
  <h1 class="page-title">HTML EMAIL SIGNATURE</h1>

  <div class="brand">
    <div class="brand-square"></div>
    <div class="brand-name">Corven Projects</div>
  </div>

  <div class="divider"></div>

  <div class="details">
    <div class="person-name">DANIEL HARTWELL</div>
    <div class="person-role">Owner</div>
    <p class="address">Corven Project, Ltd.<br>Ashby House, 42 Elmwood<br>Rd, London SE14 7QT</p>
    <ul class="contact-list">
      <li class="contact-item">
        <svg class="contact-icon" viewBox="0 0 24 24" aria-hidden="true">
          <path fill="#2a56a6" d="M6.6 2.5l3 3.2-1.8 2.6c1.2 2.8 3.3 4.9 6 6.1l2.6-1.8 3.1 3-1.7 3.4c-8.3-.6-14.4-6.8-15-15z"/>
        </svg>
        (555) 318-4620
      </li>
      <li class="contact-item">
        <svg class="contact-icon" viewBox="0 0 24 24" aria-hidden="true">
          <rect x="2" y="5" width="20" height="14" fill="none" stroke="#2a56a6" stroke-width="2"/>
          <path d="M2 5l10 8 10-8M2 19l7-7M22 19l-7-7" fill="none" stroke="#2a56a6" stroke-width="1.8"/>
        </svg>
        info@corven.com
      </li>
      <li class="contact-item">
        <svg class="contact-icon" viewBox="0 0 24 24" aria-hidden="true">
          <g fill="none" stroke="#2a56a6" stroke-width="1.6">
            <circle cx="12" cy="12" r="9.5"/>
            <ellipse cx="12" cy="12" rx="4.2" ry="9.5"/>
            <path d="M2.5 12h19M4 7h16M4 17h16"/>
          </g>
        </svg>
        www.corven.com
      </li>
    </ul>
    <div class="social-row">
      <span class="social-dot s1"></span>
      <span class="social-dot s2"></span>
      <span class="social-dot s3"></span>
      <span class="social-dot s4"></span>
    </div>
  </div>
</div>
</body>
</html>
```